Defense Attorney Business Card Design Project/ Stationary

I am looking for a distinctive business card design for my solo law practice.
I practice criminal defense, both juvenile and adult, including DUI. I am a very experienced attorney with prior military experience. The design should convey a traditional, old school flair, but not be too stodgy or uptight. Some color. My logo should appear.
Updates

Project Deadline Extended Reason: I misunderstood how this project works and I was not prepared with my logo when this project ran the first time. Added Thursday, November 13, 2014

Project Deadline Extended
Reason: I was sent overseas on military duty last year, which interrupted this project. Thank you for your participation... I hope we can get this done this week! Thank you, Neil

Target Market(s)

Regular everyday people looking for strong, knowledgeable, authoritative representation while they are faced with criminal charges. Many have never been charged with a crime before. A reassuring air is therefore desired.

Industry/Entity Type

Business

Contact Information for Business Card

My information is:
Theodore M. Quill, Attorney at Law
785 Birch Avenue Suite 300
Oakland, California 94719
Tel: (510) 384-6125
Fax: (510) 391-7802
email: neilquilllaw@mailvine.example
web: www.neilquilllaw.example

Font styles to use
Serif
Sans Serif
Decorative

Colors
0255a3
ffffff

Requirements
Must have
• Sharp lines, bold elements. Conservative use of colors, such as deep blues, burgundy, grays for example.
• While my logo says "Neil Quill", it should be modified to show "Theodore M. Quill".
Should not have
• Cliche imagery such as scales of justice, gavels, Statue of Liberty, etc.

```html
<!DOCTYPE html>
<html lang="en">
<head>
<meta charset="utf-8">
<title>Theodore M. Quill – Attorney at Law Business Card</title>
<link rel="stylesheet" href="https://fonts.googleapis.com/css2?family=Spectral+SC:wght@500;600&family=Mulish:wght@500&display=swap">
<style>
  :root {
    --burgundy: #8a1420;
    --burgundy-deep: #6e0a12;
    --burgundy-light: #9a1a26;
    --paper: #ffffff;
    --ink: #111111;
    --backdrop: #b9b7b8;
  }
  * { margin: 0; padding: 0; box-sizing: border-box; }
  html, body { width: 1200px; height: 1000px; overflow: hidden; }
  body { background: var(--backdrop); position: relative; }

  .card { position: absolute; overflow: hidden; }

  /* Front */
  .card--front { left: 47px; top: 25px; width: 775px; height: 455px; background: var(--paper); }
  .front__emblem {
    position: absolute; left: 195px; top: 70px; width: 410px; height: 195px;
    background: linear-gradient(90deg, var(--burgundy-deep), var(--burgundy-light));
    border-radius: 6px;
  }
  .front__name {
    position: absolute; left: 118px; top: 272px; width: 532px; text-align: center;
    font-family: "Spectral SC", serif; font-weight: 600; font-size: 46px;
    color: var(--burgundy); letter-spacing: 0.5px; white-space: nowrap;
  }
  .front__rule { position: absolute; left: 118px; top: 331px; width: 532px; height: 2px; background: var(--burgundy); }
  .front__band {
    position: absolute; left: 0; top: 420px; width: 775px; height: 35px;
    background: linear-gradient(90deg, var(--burgundy-deep), var(--burgundy-light) 50%, var(--burgundy-deep));
  }
  .front__tab {
    position: absolute; left: 328px; top: 397px; width: 403px; height: 40px;
    border-radius: 16px 16px 0 0;
    background: linear-gradient(90deg, var(--burgundy-deep), var(--burgundy-light) 55%, var(--burgundy-deep));
  }

  .title {
    font-family: "Spectral SC", serif; font-weight: 500; letter-spacing: 3px; white-space: nowrap;
    position: absolute; text-align: center; z-index: 3; line-height: 1.2;
  }
  .title small { font-size: 0.72em; letter-spacing: 2px; }
  .front__title { left: 328px; top: 403px; width: 403px; font-size: 26px; color: var(--paper); }

  /* Back */
  .card--back {
    left: 375px; top: 517px; width: 783px; height: 448px;
    background: linear-gradient(90deg, var(--burgundy-deep), var(--burgundy-light) 50%, var(--burgundy-deep));
  }
  .back__emblem {
    position: absolute; left: 0; top: 12px; width: 490px; height: 310px;
    background: radial-gradient(ellipse at 45% 40%, rgba(90,0,8,0.55), rgba(90,0,8,0) 70%);
  }
  .back__name {
    position: absolute; left: 300px; top: 212px; width: 440px; text-align: right;
    font-family: "Spectral SC", serif; font-weight: 600; font-size: 40px;
    color: var(--paper); white-space: nowrap; z-index: 2;
  }
  .back__tab {
    position: absolute; left: 293px; top: 301px; width: 444px; height: 30px;
    border-radius: 14px 14px 0 0; background: var(--paper); z-index: 1;
  }
  .back__title { left: 293px; top: 302px; width: 444px; font-size: 23px; color: var(--burgundy); }
  .back__contact {
    position: absolute; left: 0; top: 321px; width: 783px; height: 87px; background: var(--paper);
    font-family: "Mulish", sans-serif; font-weight: 500; font-size: 17px; color: var(--ink);
    padding: 30px 14px 0 20px; line-height: 26px;
    display: flex; justify-content: space-between; z-index: 1;
  }
  .contact__col { white-space: nowrap; }
</style>
</head>
<body>
  <section class="card card--front" aria-label="Business card front">
    <div class="front__emblem" role="img" aria-label="Firm logo emblem"></div>
    <h1 class="front__name">Theodore M. Quill</h1>
    <div class="front__rule"></div>
    <div class="front__band"></div>
    <div class="front__tab"></div>
    <p class="title front__title">ATTORNEY <small>AT</small> LAW</p>
  </section>

  <section class="card card--back" aria-label="Business card back">
    <div class="back__emblem" role="img" aria-label="Faint logo emblem decoration"></div>
    <h2 class="back__name">Theodore M. Quill</h2>
    <div class="back__tab"></div>
    <div class="back__contact">
      <div class="contact__col">
        <div>[a] 785 Birch Avenue Suite 300 Oakland, California 94719</div>
        <div>[e] neilquilllaw@mailvine.example&nbsp; [w] www.neilquilllaw.example</div>
      </div>
      <div class="contact__col">
        <div>[t] (510) 384-6125</div>
        <div>[f] (510) 391-7802</div>
      </div>
    </div>
    <p class="title back__title">ATTORNEY <small>AT</small> LAW</p>
  </section>
</body>
</html>
```